Vornel Wellness Business Card

A Double Sided Business Card

I am a private company in Melbourne, Australia, working in the Health industry. I am a nutritionist and lifestyle coach, whom specialises in using raw foods ie. fruits/nuts/vegetables to help heal my clients and enable them to achieve their ultimate state of health.

I want a sophisticated design and colour for my card that appeals to both men and women from teenage through to elderly.

Front of Card:

Red apple peel spiral in the shape of an apple. I would like a leaf/leaves coming off the stem of the apple. Please see attachments for example.

***On Right Hand side of Image is business Name: Vornel Wellness

Underneath LOGO use slogan " Let Food Be Your Medicine"

***Use Deep Red and Blues for Text Colouring

Back of Card:

Marisol Dekkert
Nutritional Specialist and Lifestyle Coach

Specialising in: Diseased Conditions
Weight Management
Achieving your Ultimate State of Health

enquiries@vornelwellness.com.au 0457 396 504

**Make sure the front design of the card flows onto the back.
Updates

Email address has been amended, Also more specific details have been given for apple peel Image, and another image attached as example of Leaf on stem of apple.

I little more insight into what sort of feel were trying to create. We're apart of the health industry, and we want the card to have a medical/clinical feeling about it.

Target Market(s)

Males and Females from teenages to elderly

Industry/Entity Type

Business

Requirements
Must have
• Red Apple Peel Spiral, in the shape of an apple, with a leaf/leaves attached to stem.
***Must be in the shape of an apple
***Please use coloring on inside of apple peel to resemble inside of an apple.
Nice to have
• I would like my card to have a clinical feel.
Should not have
• We don't want the image of the apple to look like a Christmas decoration

```html
<!DOCTYPE html>
<html lang="en">
<head>
<meta charset="utf-8">
<title>Vornel Wellness Business Card</title>
<link rel="stylesheet" href="https://fonts.googleapis.com/css2?family=Quicksand:wght@500;600;700&display=swap">
<style>
  :root {
    --backdrop: #eceae6;
    --card: #ffffff;
    --swoosh-light: #e6e6e8;
    --swoosh-dark: #a9a9ad;
    --brand-red: #e0262d;
    --brand-blue: #3a4aa0;
    --ink-navy: #2b2f6b;
    --ink-body: #3a3d5c;
    --logo-circle: #d62a2f;
  }
  * { box-sizing: border-box; margin: 0; padding: 0; }
  html, body { width: 1200px; height: 900px; overflow: hidden; }
  body {
    background: var(--backdrop);
    font-family: "Quicksand", sans-serif;
    position: relative;
  }
  .card {
    position: absolute;
    width: 620px;
    height: 370px;
    background: var(--card);
    box-shadow: 0 10px 28px rgba(0,0,0,0.18);
    overflow: hidden;
  }
  .card--back { left: 40px; top: 60px; }
  .card--front { left: 540px; top: 470px; }
  .card__swoosh { position: absolute; inset: 0; width: 100%; height: 100%; }

  /* Back side */
  .back__mark {
    position: absolute; right: 46px; top: 30px;
    width: 50px; height: 50px; border-radius: 50%;
    background: var(--logo-circle);
  }
  .back__details {
    position: absolute; left: 0; right: 0; top: 112px;
    text-align: center;
  }
  .back__name { color: var(--brand-red); font-size: 30px; font-weight: 500; letter-spacing: 0.5px; }
  .back__role { color: var(--ink-navy); font-size: 18px; font-weight: 600; line-height: 1.1; }
  .back__heading { color: var(--brand-blue); font-size: 20px; font-weight: 600; margin-top: 14px; }
  .back__specialties { list-style: none; color: var(--ink-body); font-size: 16px; font-weight: 500; line-height: 1.4; }
  .back__specialties li { display: inline; margin: 0 4px; }
  .back__specialties li::before { content: "·"; }
  .back__specialties .line-break { display: block; }
  .back__contact {
    position: absolute; left: 40px; bottom: 30px;
    list-style: none; color: var(--ink-body); font-size: 17px; font-weight: 500;
  }
  .back__contact li { display: flex; align-items: center; gap: 8px; margin-top: 6px; }
  .contact-icon { width: 24px; height: 24px; flex: none; }

  /* Front side */
  .front__lockup {
    position: absolute; left: 66px; top: 120px;
    display: flex; align-items: center; gap: 18px;
  }
  .front__circle {
    width: 128px; height: 128px; border-radius: 50%;
    background: var(--logo-circle);
    flex: none;
  }
  .front__name { color: var(--brand-red); font-size: 36px; font-weight: 700; line-height: 1; white-space: nowrap; }
  .front__slogan { color: var(--brand-blue); font-size: 18px; font-weight: 600; margin-top: 6px; white-space: nowrap; }
</style>
</head>
<body>

<section class="card card--back" aria-label="Back of business card">
  <svg class="card__swoosh" viewBox="0 0 620 370" aria-hidden="true">
    <defs>
      <linearGradient id="swooshBackA" x1="0" y1="0" x2="1" y2="1">
        <stop offset="0" stop-color="var(--swoosh-dark)"/>
        <stop offset="1" stop-color="var(--swoosh-light)"/>
      </linearGradient>
      <linearGradient id="swooshBackB" x1="1" y1="1" x2="0" y2="0">
        <stop offset="0" stop-color="var(--swoosh-dark)"/>
        <stop offset="1" stop-color="var(--swoosh-light)"/>
      </linearGradient>
    </defs>
    <path d="M0 0 H170 C80 30 20 110 0 240 Z" fill="url(#swooshBackA)"/>
    <path d="M620 370 H440 C540 340 600 250 620 130 Z" fill="url(#swooshBackB)"/>
  </svg>

  <span class="back__mark" aria-hidden="true"></span>

  <div class="back__details">
    <h1 class="back__name">Marisol Dekkert</h1>
    <p class="back__role">Nutritional Specialist<br>Lifestyle Coach</p>
    <h2 class="back__heading">Specialising in:</h2>
    <ul class="back__specialties">
      <li>Diseased Conditions</li>
      <li>Weight Management</li>
      <li class="line-break">Achieving your Ultimate State of Health</li>
    </ul>
  </div>

  <ul class="back__contact">
    <li>
      <svg class="contact-icon" viewBox="0 0 24 24" aria-hidden="true">
        <circle cx="12" cy="12" r="12" fill="var(--brand-red)"/>
        <g fill="none" stroke="#fff" stroke-width="1.3">
          <circle cx="12" cy="12" r="6.5"/>
          <ellipse cx="12" cy="12" rx="3" ry="6.5"/>
          <line x1="5.5" y1="12" x2="18.5" y2="12"/>
        </g>
      </svg>
      enquiries@vornelwellness.com.au
    </li>
    <li>
      <svg class="contact-icon" viewBox="0 0 24 24" aria-hidden="true">
        <circle cx="12" cy="12" r="12" fill="var(--brand-red)"/>
        <path d="M8.2 6.5l2 2.4-1.1 1.4c.8 1.8 2 3 3.8 3.8l1.4-1.1 2.4 2-1.1 1.8c-4.4-.5-8.1-4.2-8.6-8.6z" fill="#fff"/>
      </svg>
      0457 396 504
    </li>
  </ul>
</section>

<section class="card card--front" aria-label="Front of business card">
  <svg class="card__swoosh" viewBox="0 0 620 370" aria-hidden="true">
    <defs>
      <linearGradient id="swooshFrontA" x1="0" y1="0" x2="1" y2="1">
        <stop offset="0" stop-color="var(--swoosh-dark)"/>
        <stop offset="1" stop-color="var(--swoosh-light)"/>
      </linearGradient>
      <linearGradient id="swooshFrontB" x1="1" y1="1" x2="0" y2="0">
        <stop offset="0" stop-color="var(--swoosh-dark)"/>
        <stop offset="1" stop-color="var(--swoosh-light)"/>
      </linearGradient>
    </defs>
    <path d="M0 0 H170 C80 30 20 110 0 240 Z" fill="url(#swooshFrontA)"/>
    <path d="M620 370 H440 C540 340 600 250 620 130 Z" fill="url(#swooshFrontB)"/>
  </svg>

  <div class="front__lockup">
    <span class="front__circle" aria-hidden="true"></span>
    <div class="front__wordmark">
      <p class="front__name">Vornel Wellness</p>
      <p class="front__slogan">Let Food Be Your Medicine</p>
    </div>
  </div>
</section>

</body>
</html>
```